NEW Wordpress Website Design for a Dynamic Long Term Healthcare Company in Hawaii

I would like a new website design for my current company, Marlow Health Collective, which has two different brands - Marlow Homecare and Marlow Senior Living. You can see the current website at www.marlowhealth-example.com. The website should be built using Wordpress Software and the Framewise theme. The website should have a local Hawaii island/tropical feel, but look professional for healthcare. I'm looking for something fresh, and want the designer to select colors, styles, etc.

In the Header, on all pages, I would like a menu that includes Home Care, Senior Living, Rates, and About Us.
Under each of the Header Menu Titles, I would like these drop downs included:
Home Care (drop down pages)- Nurse Aide Care, 24-Hour Home Care, Skilled Nursing, Lifestyle Aide, Hospice at Home, Bathing & Meal Service.
Senior Living (drop down pages) - Long-Term Stay, Short-Term Stay.
Rates (drop down page) - Rates.
About Us (drop down pages) - Our Mission, Ohana Talk, About Dana Marlow.

In the footer, on all pages, you should include the address: 248 Pueo Lane, Suite 310, Honolulu, HI 96817. Phone number: 808-555-0172
The footer should also include buttons for a page called Learn, Caregiver Jobs, and each of the service page links to include: Nurse Aide Care, 24-Hour Home Care, Skilled Nursing, Lifestyle Aide, Hospice at Home, Bathing & Meal Service.
Please don't take the current website and redesign a few aspects. I'm looking for a completely different look and feel.

Target Market(s)

40-80 year olds

Industry/Entity Type

Long Term Healthcare

Coding

Coded - Design and coding required

Requirements
Should not have
• Our existing website as a template. We are looking for a complete redesign. Thank you.

```html
<!DOCTYPE html>
<html lang="en">
<head>
<meta charset="utf-8">
<title>Marlow Health Collective — Homecare &amp; Senior Living</title>
<link href="https://fonts.googleapis.com/css2?family=Marcellus&family=Montserrat:wght@400;500;600;700&family=Quicksand:wght@500;600;700&display=swap" rel="stylesheet">
<style>
:root{
  --teal:#2aa397;
  --teal-dark:#1f8a80;
  --orange:#f5821f;
  --orange-soft:#f8a03c;
  --red:#d9452a;
  --ink:#1f1f1f;
  --text:#4a4a4a;
  --muted:#8a8a8a;
  --line:#e4e0d8;
  --cream:#fbf7ee;
  --white:#ffffff;
}
*{box-sizing:border-box;margin:0;padding:0}
html,body{width:1200px;height:4511px;overflow:hidden}
body{position:relative;background:var(--white);font-family:"Montserrat",sans-serif;color:var(--text)}
.abs{position:absolute}
.photo{position:absolute;display:block}
.btn{position:absolute;display:flex;align-items:center;justify-content:center;border-radius:30px;font-family:"Montserrat",sans-serif;font-weight:600;font-size:14px;letter-spacing:.5px;color:var(--white);text-transform:uppercase}
.btn--orange{background:linear-gradient(180deg,#f79a2e,#ef7a18)}
.btn--teal{background:var(--teal)}
.squiggle{position:absolute;width:64px;height:10px}
.heading{font-family:"Quicksand",sans-serif;font-weight:600;color:var(--ink)}

/* header */
.site-header{position:absolute;left:0;top:0;width:1200px;height:90px;z-index:5}
.brand{position:absolute;left:100px;top:16px;display:flex;align-items:center;gap:10px}
.brand__mark{width:46px;height:46px;background:var(--orange);border-radius:8px}
.brand__name{font-family:"Quicksand",sans-serif;font-weight:700;font-size:40px;color:var(--red);line-height:1}
.main-nav{position:absolute;left:390px;top:36px;display:flex;gap:40px;font-size:14px;font-weight:500;color:#333}
.main-nav span::after{content:"";display:inline-block;width:6px;height:6px;border-right:1.5px solid #999;border-bottom:1.5px solid #999;transform:rotate(45deg);margin-left:6px;position:relative;top:-3px}
.call{position:absolute;left:923px;top:23px;width:186px;height:40px;border-radius:22px;background:var(--orange);color:#fff;font-weight:700;font-size:15px;display:flex;align-items:center;justify-content:center;gap:8px}
.call__dot{width:20px;height:20px;border-radius:50%;background:#fff;display:flex;align-items:center;justify-content:center}

/* hero */
.hero{position:absolute;left:0;top:0;width:1200px;height:736px;background:linear-gradient(180deg,#fdfbf3 0%,#f3eed8 30%,#d9b98a 55%,#b88e5b 75%,#8e5f3a 100%)}
.hero__eyebrow{position:absolute;left:0;width:1200px;top:128px;text-align:center;font-family:"Montserrat",sans-serif;font-weight:500;font-size:28px;color:var(--red);letter-spacing:.5px}
.hero__eyebrow::before,.hero__eyebrow::after{content:"";display:inline-block;width:30px;height:2px;background:var(--red);vertical-align:middle;margin:0 10px}
.hero__title{position:absolute;left:0;width:1200px;top:160px;text-align:center;font-family:"Marcellus",serif;font-size:56px;color:#222}

/* mission card */
.mission{position:absolute;left:149px;top:640px;width:908px;height:394px;background:linear-gradient(135deg,#33b3a5,#1f9488);border-radius:34px 0 80px 0;z-index:3}
.mission__frame{position:absolute;left:14px;top:14px;right:14px;bottom:14px;border:1.5px solid rgba(255,255,255,.7);border-radius:28px 0 70px 0}
.mission__icon{position:absolute;left:432px;top:34px;width:46px;height:46px;border:3px solid #fff;border-radius:10px}
.mission__title{position:absolute;left:0;width:908px;top:92px;text-align:center;font-family:"Quicksand",sans-serif;font-weight:600;font-size:46px;color:#fff}
.mission__text{position:absolute;left:100px;width:708px;top:162px;text-align:center;font-size:16.5px;line-height:27px;color:#fff}
.mission__btn{position:absolute;left:370px;top:292px;width:174px;height:42px;border:1.5px solid #fff;border-radius:22px;color:#fff;font-size:13px;font-weight:600;display:flex;align-items:center;justify-content:center}

.divider-v{position:absolute;left:596px;top:1034px;width:1px;height:1076px;background:#d8d2c6}

/* home care */
.home-care{position:absolute;left:0;top:1098px;width:1200px;height:580px;background:linear-gradient(90deg,#fbf8f0,#fdfbf6)}
.service-list{position:absolute;display:grid;column-gap:32px;row-gap:20px;font-size:15px;font-weight:600;color:#333}
.service-list li{list-style:none;display:flex;align-items:center;gap:10px;white-space:nowrap}
.chev{width:8px;height:8px;border-right:2.5px solid var(--orange);border-top:2.5px solid var(--orange);transform:rotate(45deg)}
.chev--teal{border-color:var(--teal)}

/* senior */
.senior{position:absolute;left:0;top:1678px;width:1200px;height:617px;background:#fdfbf7}

/* testimonials */
.testimonials{position:absolute;left:0;top:2295px;width:1200px;height:596px;background:linear-gradient(180deg,#f4efe0,#f9f5ea 60%,#fbf2e4)}
.t-card{position:absolute;background:#fff;box-shadow:0 4px 18px rgba(0,0,0,.12);font-size:12.5px;line-height:19px;color:#444;text-align:center}
.t-card--main{left:347px;top:181px;width:540px;height:322px;font-size:16.5px;line-height:24px;padding:48px 50px 0;color:#333}
.quote{position:absolute;font-family:Georgia,serif;font-size:38px;color:var(--orange);font-weight:700;line-height:1}
.review-link{display:block;margin-top:14px;font-weight:700;font-size:15px;text-decoration:underline;color:#222}
.review-dot{position:absolute;width:26px;height:26px;border-radius:50%;border:3px solid #6aa1e8}
.arrow{position:absolute;width:34px;height:34px;border-radius:50%;background:var(--teal);display:flex;align-items:center;justify-content:center}

/* blogs */
.blog-date{display:inline-flex;align-items:center;gap:5px;background:#e5751a;color:#fff;font-size:11px;font-weight:700;padding:3px 8px;border-radius:3px}
.blog-small{position:absolute;left:650px;width:464px;height:189px;border:1px solid #ddd;background:#fff}
.blog-small__body{position:absolute;left:247px;top:24px;width:200px}
.blog-small__title{font-size:11.5px;font-weight:700;color:#222;line-height:15px;margin-top:10px}
.blog-small__text{font-size:10.5px;color:#777;line-height:14px;margin-top:8px}
.blog-small__more{font-size:10px;font-weight:700;color:var(--orange);text-decoration:underline;margin-top:10px;display:block}

/* schedule */
.schedule{position:absolute;left:96px;top:3539px;width:1004px;height:534px;border-radius:60px 0 60px 0;overflow:hidden;background:linear-gradient(90deg,#f7931e 0%,#f59a2a 40%,#e8c38f 62%,#c9c98a 100%)}
.field{position:absolute;background:#fff;border:1px solid #e7e7e7;font-size:13px;color:#555;padding:14px 18px}

/* footer */
.footer{position:absolute;left:0;top:4073px;width:1200px;height:438px;background:linear-gradient(180deg,#fff,#fbf9f3)}
.f-col-line{position:absolute;top:60px;width:1px;height:330px;background:#e2ddd2}
.f-heading{position:absolute;font-family:"Quicksand",sans-serif;font-weight:600;font-size:21px;color:#222}
.f-heading::before{content:"";position:absolute;left:-14px;top:4px;width:2px;height:22px;background:var(--orange)}
.f-links{position:absolute;list-style:none;font-size:13px;color:#444}
.f-links li{height:31px;display:flex;align-items:center;gap:8px}
.f-links li::before{content:"›";color:var(--orange);font-size:14px}
.f-btn{position:absolute;left:156px;width:166px;height:33px;font-size:11px;font-weight:700;display:flex;align-items:center;justify-content:center;gap:6px;text-transform:uppercase}
.social{width:30px;height:30px;border-radius:50%}
</style>
</head>
<body>

<!-- hero -->
<section class="hero">
  <div class="photo" role="img" aria-label="Three women knitting together on a sofa in a bright island living room" style="left:0;top:300px;width:1200px;height:436px;background:linear-gradient(180deg,rgba(247,242,224,0),rgba(190,140,90,.35) 40%,rgba(140,90,55,.6))"></div>
  <p class="hero__eyebrow">MARLOW HEALTH COLLECTIVE</p>
  <h1 class="hero__title">Homecare &amp; Senior Living</h1>
  <div class="btn btn--orange" style="left:506px;top:248px;width:188px;height:50px">View Rates&nbsp;›</div>
</section>

<header class="site-header">
  <div class="brand"><span class="brand__mark"></span><span class="brand__name">Marlow</span></div>
  <nav class="main-nav"><span>HOME CARE</span><span>SENIOR LIVING</span><span>RATES</span><span>ABOUT US</span></nav>
  <div class="call"><span class="call__dot"><svg width="12" height="12" viewBox="0 0 24 24"><path fill="#f5821f" d="M6.6 10.8a15 15 0 006.6 6.6l2.2-2.2c.3-.3.7-.4 1-.2 1.1.4 2.3.6 3.6.6.6 0 1 .4 1 1V20c0 .6-.4 1-1 1A17 17 0 013 4c0-.6.4-1 1-1h3.5c.6 0 1 .4 1 1 0 1.3.2 2.5.6 3.6.1.3 0 .7-.2 1z"/></svg></span>(808) 555-0172</div>
</header>

<section class="mission">
  <div class="mission__frame"></div>
  <div class="mission__icon"></div>
  <h2 class="mission__title">Marlow Health Collective</h2>
  <p class="mission__text">At Marlow Health Collective, our mission is to provide compassionate and professional long-term healthcare services that empower individuals to maintain their highest level of independence, health, and well-being in the comfort of their own homes or ours, either through our licensed home healthcare agency</p>
  <div class="mission__btn">LEARN MORE</div>
</section>

<!-- home care -->
<section class="home-care">
  <div class="photo" role="img" aria-label="Caregiver in teal scrubs helping an older man dress in his bedroom" style="left:0;top:0;width:596px;height:580px;background:linear-gradient(135deg,#c9b79a,#a88f6c 45%,#6fa9b5 70%,#d8cdb8)"></div>
  <h2 class="heading abs" style="left:654px;top:116px;font-size:46px">Home Care</h2>
  <svg class="squiggle" style="left:654px;top:176px" viewBox="0 0 64 10"><path d="M2 7 Q18 1 32 5 T62 3" stroke="#f5821f" stroke-width="3.5" fill="none" stroke-linecap="round"/></svg>
  <p class="abs" style="left:654px;top:196px;width:420px;font-size:15px;line-height:23px;color:#444">Marlow Homecare understands that every person's care journey is unique. We tailor our in-home services to meet the diverse nurturing experience</p>
  <ul class="service-list" style="left:660px;top:298px;grid-template-columns:196px 210px">
    <li><span class="chev"></span>Nurse Aide Care</li><li><span class="chev"></span>Lifestyle Aide</li>
    <li><span class="chev"></span>24-Hour Home Care</li><li><span class="chev"></span>Hospice at Home</li>
    <li><span class="chev"></span>Skilled Nursing</li><li><span class="chev"></span>Bathing &amp; Meal Service</li>
  </ul>
  <div class="btn btn--orange" style="left:650px;top:436px;width:184px;height:50px">Learn More&nbsp;›</div>
</section>

<!-- senior living -->
<section class="senior">
  <div class="photo" role="img" aria-label="Nurse and resident sharing a photo album on a couch near a sunny lanai" style="left:596px;top:0;width:604px;height:617px;background:linear-gradient(135deg,#e9e1cf,#b9a684 40%,#4f86b8 60%,#8bb98c)"></div>
  <div class="abs" style="left:594px;top:156px;width:3px;height:278px;background:var(--teal)"></div>
  <h2 class="heading abs" style="left:112px;top:146px;font-size:46px">Senior Living</h2>
  <svg class="squiggle" style="left:112px;top:206px" viewBox="0 0 64 10"><path d="M2 7 Q18 1 32 5 T62 3" stroke="#2aa397" stroke-width="3.5" fill="none" stroke-linecap="round"/></svg>
  <p class="abs" style="left:112px;top:242px;width:440px;font-size:16px;line-height:27px;color:#444">Marlow Senior Living creates a warm, supportive, and enriching care home environment where seniors can thrive in their golden years. We provide residential care that promotes well-being, connection, and dignity of each individual.</p>
  <ul class="service-list" style="left:112px;top:402px;grid-template-columns:212px 200px">
    <li><span class="chev chev--teal"></span>LONG-TERM STAY</li><li><span class="chev chev--teal"></span>SHORT-TERM STAY</li>
  </ul>
  <div class="btn btn--teal" style="left:110px;top:460px;width:184px;height:50px">Learn More&nbsp;›</div>
</section>

<div class="divider-v"></div>

<!-- testimonials -->
<section class="testimonials">
  <h2 class="heading abs" style="left:0;width:1200px;top:68px;text-align:center;font-size:48px">Testimonials</h2>
  <svg class="squiggle" style="left:568px;top:132px" viewBox="0 0 64 10"><path d="M2 7 Q18 1 32 5 T62 3" stroke="#2aa397" stroke-width="3.5" fill="none" stroke-linecap="round"/></svg>
  <div class="t-card" style="left:165px;top:216px;width:200px;height:236px;padding:28px 14px 0 34px;text-align:left">Lorem ipsum dolor sit amet, sed do eiusmod tempor magna aliqua. Ut enim ad exercitation ullamco commodo consequat. reprehenderit in voluptate</div>
  <div class="t-card" style="left:870px;top:216px;width:202px;height:236px;padding:28px 20px 0 30px;text-align:left">consectetur adipiscing elit, tempor ut labore et dolore ad veniam, quis nostrud nisi ut aliquip ex ea aute irure dolor in esse cillum dolore eu<div class="review-dot" style="left:158px;top:182px;width:20px;height:20px"></div></div>
  <div class="t-card t-card--main">
    <span class="quote" style="left:44px;top:40px">“</span>
    Lorem ipsum dolor sit amet, consectetur adipiscing elit, sed do eiusmod tempor incididunt ut labore et dolore magna aliqua. Ut enim ad minim veniam, quis nostrud exercitation ullamco laboris nisi ut aliquip ex ea commodo consequat. Duis aute irure dolor in reprehenderit in voluptate velit esse cillum dolore eu fugiat nulla
    <span class="review-link">Verified Review</span>
    <span class="quote" style="left:478px;top:200px">”</span>
    <div class="review-dot" style="left:482px;top:264px"></div>
  </div>
  <div class="arrow" style="left:102px;top:319px"><svg width="16" height="16" viewBox="0 0 16 16"><path d="M14 8H3M7 3L2 8l5 5" stroke="#fff" stroke-width="1.8" fill="none"/></svg></div>
  <div class="arrow" style="left:1104px;top:319px"><svg width="16" height="16" viewBox="0 0 16 16"><path d="M2 8h11M9 3l5 5-5 5" stroke="#fff" stroke-width="1.8" fill="none"/></svg></div>
</section>

<!-- blogs -->
<section>
  <h2 class="heading abs" style="left:131px;top:2940px;font-size:46px">Latest Blogs</h2>
  <svg class="squiggle" style="left:131px;top:3000px" viewBox="0 0 64 10"><path d="M2 7 Q18 1 32 5 T62 3" stroke="#2aa397" stroke-width="3.5" fill="none" stroke-linecap="round"/></svg>
  <div class="photo" role="img" aria-label="Caregiver pouring a drink for seniors at a dining table in a care home" style="left:131px;top:3043px;width:505px;height:400px;background:linear-gradient(180deg,#b4935f,#8a6a43 55%,#3a2a1c)"></div>
  <div class="abs" style="left:166px;top:3334px;width:420px;color:#fff">
    <span class="blog-date">◷ 15 SEP 2024</span>
    <p style="font-size:16px;font-weight:700;line-height:26px;margin-top:10px">Intentional Misuse of Social Media App May Lead to Developer Liability</p>
  </div>
  <div class="blog-small" style="top:3043px">
    <div class="photo" role="img" aria-label="Caregiver walking with two seniors outdoors in a garden" style="left:0;top:0;width:223px;height:189px;background:linear-gradient(135deg,#7fa564,#c4c2a6)"></div>
    <div class="blog-small__body"><span class="blog-date">◷ 04 SEP 2024</span><p class="blog-small__title">Lorem ipsum dolor sit amet consectetur adipiscing elit</p><p class="blog-small__text">Duis aute irure dolor in reprehenderit in voluptate velit esse cillum dolore eu fugiat nulla</p><span class="blog-small__more">LEARN MORE</span></div>
  </div>
  <div class="blog-small" style="top:3250px">
    <div class="photo" role="img" aria-label="Portrait of a smiling caregiver" style="left:0;top:0;width:223px;height:189px;background:linear-gradient(135deg,#d8d4cc,#9c7158)"></div>
    <div class="blog-small__body"><span class="blog-date">◷ 01 SEP 2024</span><p class="blog-small__title">Lorem ipsum dolor sit amet consectetur adipiscing elit</p><p class="blog-small__text">Duis aute irure dolor in reprehenderit in voluptate velit esse cillum dolore eu fugiat nulla</p><span class="blog-small__more">LEARN MORE</span></div>
  </div>
</section>

<!-- schedule -->
<section class="schedule">
  <div class="photo" role="img" aria-label="Caregiver serving breakfast to an older couple at a kitchen table" style="left:482px;top:0;width:522px;height:534px;background:linear-gradient(90deg,rgba(245,154,42,0),rgba(190,170,120,.5) 30%,rgba(150,140,110,.55))"></div>
  <h2 class="abs" style="left:93px;top:84px;font-family:'Quicksand',sans-serif;font-weight:600;font-size:34px;line-height:44px;color:#fff">Schedule a Complimentary<br>are Consultation</h2>
  <svg class="squiggle" style="left:93px;top:180px" viewBox="0 0 64 10"><path d="M2 7 Q18 1 32 5 T62 3" stroke="#fff" stroke-width="3.5" fill="none" stroke-linecap="round"/></svg>
  <div class="field" style="left:93px;top:193px;width:207px;height:43px">First Name</div>
  <div class="field" style="left:310px;top:193px;width:205px;height:43px">Last Name</div>
  <div class="field" style="left:93px;top:247px;width:207px;height:44px">Email address</div>
  <div class="field" style="left:310px;top:247px;width:205px;height:44px">Phone Number</div>
  <div class="field" style="left:93px;top:301px;width:422px;height:100px">Message</div>
  <div class="btn btn--teal" style="left:93px;top:415px;width:196px;height:42px;font-size:13px">Send Message&nbsp;›</div>
</section>

<!-- footer -->
<footer class="footer">
  <div class="abs" style="left:166px;top:62px;width:140px;text-align:center">
    <div style="width:52px;height:52px;background:var(--orange);border-radius:10px;margin:0 auto 10px"></div>
    <div style="font-family:'Quicksand',sans-serif;font-weight:700;font-size:44px;color:var(--red);line-height:1">Marlow</div>
  </div>
  <div class="f-btn" style="top:212px;border:1.5px solid var(--orange);color:var(--orange)">Learn</div>
  <div class="f-btn" style="top:258px;background:var(--orange);color:#fff">Caregiver Jobs</div>

  <div class="f-col-line" style="left:391px"></div>
  <div class="f-col-line" style="left:601px"></div>
  <div class="f-col-line" style="left:829px"></div>

  <h3 class="f-heading" style="left:415px;top:68px">Navigation</h3>
  <ul class="f-links" style="left:415px;top:106px"><li>Home Care</li><li>Senior Living</li><li>Rates</li><li>About Us</li></ul>

  <h3 class="f-heading" style="left:622px;top:68px">Services</h3>
  <ul class="f-links" style="left:622px;top:102px"><li>Nurse Aide Care</li><li>24-Hour Home Care</li><li>Skilled Nursing</li><li>Lifestyle Aide</li><li>Hospice at Home</li><li>Bathing &amp; Meal Service</li></ul>

  <h3 class="f-heading" style="left:850px;top:68px">Contact Us</h3>
  <div class="abs" style="left:850px;top:108px;display:flex;gap:14px;font-size:13px;line-height:18px;color:#333">
    <svg width="30" height="30" viewBox="0 0 30 30"><circle cx="15" cy="15" r="15" fill="#2aa397"/><path d="M15 7a5 5 0 00-5 5c0 4 5 10 5 10s5-6 5-10a5 5 0 00-5-5z" fill="#fff"/><circle cx="15" cy="12" r="2" fill="#2aa397"/></svg>
    <p>248 Pueo Lane, Suite 310,<br>Honolulu, HI 96817</p>
  </div>
  <div class="abs" style="left:850px;top:162px;display:flex;gap:14px;font-size:13px;line-height:18px;color:#333">
    <svg width="30" height="30" viewBox="0 0 30 30"><circle cx="15" cy="15" r="15" fill="#2aa397"/><path d="M11.5 13.3a8 8 0 003.5 3.5l1.2-1.2c.2-.2.4-.2.6-.1.6.2 1.2.3 1.9.3.3 0 .5.2.5.5v1.9c0 .3-.2.5-.5.5A9 9 0 019.7 9.5c0-.3.2-.5.5-.5h1.9c.3 0 .5.2.5.5 0 .7.1 1.3.3 1.9 0 .2 0 .4-.2.6z" fill="#fff"/></svg>
    <p>Phone number<br><b style="font-size:15px">808-555-0172</b></p>
  </div>
  <div class="abs" style="left:856px;top:230px;display:flex;gap:8px">
    <span class="social" style="background:#f5821f"></span><span class="social" style="background:#2aa397"></span><span class="social" style="background:#2aa397"></span><span class="social" style="background:#2aa397"></span>
  </div>

  <div class="abs" style="left:30px;top:372px;width:1140px;height:1px;background:#ddd"></div>
  <p class="abs" style="left:0;width:1200px;top:396px;text-align:center;font-size:11px;color:#444">Copyright © 2024 <u>Marlow Health Collective</u>. All Right Reserved</p>
</footer>

</body>
</html>
```